Tolvik Commercial Cleaning is lookong for a new business card design.

A fresh new design that's professional and stylish. We need a serious upgrade to our business cards. I have included pictures of our existing ones. Our clients include professional individuals and business owners. We woupdblike something professional and upbeat. Please have fun and see what you come uo with.

Target Market(s)

Property managers, business owners, facility managers and other similar professionals

Industry/Entity Type

Janitorial

Contact Information for Business Card

Name, cell, office number, email, web address

Font styles to use
Sans Serif

Colors

Designer to choose colors to be used in the design.

Requirements
Must have
• please use the green color in our logo
Nice to have
• Bar code
Should not have
• Address

```html
<!DOCTYPE html>
<html lang="en">
<head>
<meta charset="utf-8">
<title>Tolvik Commercial Cleaning – Business Card</title>
<link rel="stylesheet" href="https://fonts.googleapis.com/css2?family=Comfortaa:wght@700&family=Open+Sans:ital,wght@0,400;1,400&display=swap">
<style>
  :root {
    --brand-green: #2ea84a;
    --brand-green-deep: #23903b;
    --brand-blue: #2a5aa0;
    --paper: #f7f7f5;
    --ghost: #e1e1df;
    --ink: #3c3c3c;
    --white: #ffffff;
    --stage: #e6e8e5;
  }
  * { box-sizing: border-box; margin: 0; padding: 0; }
  html, body {
    width: 1200px; height: 963px; overflow: hidden;
    background: var(--stage);
  }
  .sheet {
    width: 1200px; height: 963px;
    display: flex; flex-direction: column; align-items: center; justify-content: center;
    gap: 56px;
  }
  .card {
    position: relative; width: 700px; height: 400px;
    border-radius: 28px; overflow: hidden;
    box-shadow: 0 10px 30px rgba(0,0,0,.15);
  }

  /* Front */
  .card--front { background: var(--paper); }
  .front__brand { position: absolute; left: 56px; top: 44px; z-index: 1; }
  .brand-name {
    font-family: "Comfortaa", sans-serif; font-weight: 700;
    color: var(--brand-green); font-size: 92px; line-height: 1; letter-spacing: -2px;
  }
  .brand-line {
    font-family: "Comfortaa", sans-serif; font-weight: 700;
    color: var(--brand-blue); font-size: 21px; margin-top: 8px; letter-spacing: .3px;
  }
  .front__holder {
    position: absolute; right: 58px; top: 150px; z-index: 1;
    font-family: "Comfortaa", sans-serif; font-weight: 700;
    color: var(--brand-green); font-size: 34px;
  }
  .front__tab {
    position: absolute; right: 0; top: 232px; width: 16px; height: 28px;
    background: var(--brand-green);
  }
  .front__contacts {
    position: absolute; left: 56px; top: 222px; list-style: none; z-index: 1;
    font-family: "Open Sans", sans-serif; font-size: 17px; color: var(--ink);
  }
  .front__contacts li { display: flex; align-items: center; gap: 12px; height: 30px; }
  .front__contacts svg { width: 16px; height: 16px; flex: none; }
  .front__ghost {
    position: absolute; right: -40px; bottom: -40px;
    font-family: "Comfortaa", sans-serif; font-weight: 700;
    color: var(--ghost); font-size: 170px; line-height: 1; letter-spacing: -4px;
  }
  .front__edge {
    position: absolute; left: 0; right: 0; bottom: 0; height: 6px;
    background: var(--brand-green);
  }

  /* Back */
  .card--back {
    background: var(--brand-green);
    display: flex; flex-direction: column; align-items: center; justify-content: center;
  }
  .back__mark {
    font-family: "Comfortaa", sans-serif; font-weight: 700;
    color: var(--brand-green-deep); font-size: 150px; line-height: 1; letter-spacing: -4px;
  }
  .back__name {
    font-family: "Comfortaa", sans-serif; font-weight: 700;
    color: var(--white); font-size: 30px; margin-top: 10px;
  }
  .back__tagline {
    font-family: "Open Sans", sans-serif; font-style: italic;
    color: var(--white); font-size: 24px; margin-top: 16px;
  }
</style>
</head>
<body>
<main class="sheet">

  <section class="card card--front" aria-label="Business card front">
    <div class="front__ghost" aria-hidden="true">tolvik</div>

    <div class="front__brand">
      <div class="brand-name">tolvik</div>
      <div class="brand-line">commercial cleaning</div>
    </div>

    <div class="front__holder">mara quillen</div>
    <div class="front__tab"></div>

    <ul class="front__contacts">
      <li>
        <svg viewBox="0 0 16 16" aria-hidden="true"><path d="M4 1.5l2.2 3-1.3 1.6a8 8 0 0 0 5 5l1.6-1.3 3 2.2-1.2 2.4C7.5 14.2 1.8 8.5 1.6 2.7z" fill="var(--brand-green)"/></svg>
        (555) 014-2290
      </li>
      <li>
        <svg viewBox="0 0 16 16" aria-hidden="true"><rect x="1.5" y="3.5" width="13" height="9" rx="1" fill="none" stroke="var(--brand-green)" stroke-width="1.4"/><path d="M1.8 4l6.2 5 6.2-5" fill="none" stroke="var(--brand-green)" stroke-width="1.4"/></svg>
        mara@tolvikcleaning.com
      </li>
      <li>
        <svg viewBox="0 0 16 16" aria-hidden="true"><circle cx="8" cy="8" r="6.5" fill="none" stroke="var(--brand-green)" stroke-width="1.4"/><ellipse cx="8" cy="8" rx="2.8" ry="6.5" fill="none" stroke="var(--brand-green)" stroke-width="1.2"/><path d="M1.5 8h13M2.6 4.8h10.8M2.6 11.2h10.8" stroke="var(--brand-green)" stroke-width="1.1"/></svg>
        www.tolvikcleaning.com
      </li>
    </ul>

    <div class="front__edge"></div>
  </section>

  <section class="card card--back" aria-label="Business card back">
    <div class="back__mark">tolvik</div>
    <div class="back__name">tolvik commercial cleaning</div>
    <div class="back__tagline">spotless spaces every day</div>
  </section>

</main>
</body>
</html>
```